Indy Film Production Company/Studio

We need a business card designed from an existing logo. We are a digital studio/production company that caters to creating genre entertainment, like Action, Horror, and martial arts. The card along with the logo will be used to Brand the company from letter heads to banners. The design will also be used for postcards and Brochures. It should be professional and masculine.
Updates

Thank you to all the designers who have participated. I'm narrowing down who it will be. Thank you again.

Target Market(s)

Investors, Networks, Producers, and actors

Industry/Entity Type

Film Production

Contact Information for Business Card

Teodoro Valbuena
Producer/Writer/Director
www.kestrelpicturehouse.example

Requirements
Must have
• Website address, Facebook icon and Twitter icon possibly in the back of the card.
Nice to have
• Logline of Company: Follow The Action.

```html
<!DOCTYPE html>
<html lang="en">
<head>
<meta charset="utf-8">
<title>Kestrel Picture House – Business Card</title>
<link href="https://fonts.googleapis.com/css2?family=Roboto:ital,wght@0,400;0,700;1,700;1,900&display=swap" rel="stylesheet">
<style>
  :root {
    --backdrop: #a9a7a8;
    --brand-red: #d0322b;
    --deep-red: #c52f29;
    --paper: #f3f2f0;
    --ink: #1f1f1f;
    --charcoal: #2a2a2a;
    --white: #ffffff;
  }
  * { box-sizing: border-box; margin: 0; padding: 0; }
  html, body {
    width: 1200px; height: 1200px; overflow: hidden;
    background: var(--backdrop);
    font-family: "Roboto", Arial, sans-serif;
  }
  .canvas { position: relative; width: 1200px; height: 1200px; }

  .card { position: absolute; overflow: hidden; }

  /* Front */
  .card-front {
    left: 238px; top: 118px; width: 800px; height: 419px;
    background: var(--brand-red);
    display: flex; align-items: center; justify-content: center;
  }
  .wordmark {
    display: flex; align-items: center; gap: 14px;
    font-weight: 700; text-transform: uppercase; letter-spacing: 1px;
  }
  .wordmark-mark { width: 26px; height: 26px; }
  .card-front .wordmark { color: var(--white); font-size: 34px; }
  .card-front .wordmark-mark { background: var(--white); }

  /* Back */
  .card-back {
    left: 231px; top: 645px; width: 712px; height: 388px;
    background: var(--paper);
  }
  .wave { position: absolute; left: 0; top: 0; width: 712px; height: 388px; }
  .holder { position: absolute; left: 41px; top: 60px; }
  .holder-name {
    font-weight: 700; font-style: italic; font-size: 26px; color: var(--ink);
  }
  .holder-role { margin-top: 8px; font-size: 16px; color: var(--charcoal); }

  .card-back .wordmark {
    position: absolute; right: 64px; top: 78px;
    color: var(--brand-red); font-size: 21px; gap: 10px;
  }
  .card-back .wordmark-mark { width: 18px; height: 18px; background: var(--brand-red); }

  .contact-list { position: absolute; left: 41px; top: 204px; list-style: none; }
  .contact-list li {
    display: flex; align-items: center; gap: 18px;
    font-size: 17px; color: var(--ink); height: 27.5px;
  }
  .contact-list svg { width: 16px; height: 14px; fill: var(--brand-red); }

  .address {
    position: absolute; right: 32px; top: 302px;
    text-align: right; color: var(--white); font-size: 17px; line-height: 28.5px;
  }
</style>
</head>
<body>
<main class="canvas">

  <section class="card card-front" aria-label="Card front">
    <div class="wordmark"><span class="wordmark-mark"></span>Kestrel Picture House</div>
  </section>

  <section class="card card-back" aria-label="Card back">
    <svg class="wave" viewBox="0 0 712 388" aria-hidden="true">
      <path d="M0,318 C150,392 300,382 425,318 S625,212 712,208 L712,388 L0,388 Z" fill="var(--deep-red)"/>
      <path d="M48,336 C200,378 340,346 462,268 S642,194 712,198 L712,212 C630,212 562,240 472,296 C352,368 210,372 48,336 Z" fill="var(--charcoal)"/>
    </svg>

    <div class="holder">
      <p class="holder-name">Teodoro Valbuena</p>
      <p class="holder-role">Managing Director</p>
    </div>

    <div class="wordmark"><span class="wordmark-mark"></span>Kestrel Picture House</div>

    <ul class="contact-list">
      <li>
        <svg viewBox="0 0 16 14"><path d="M1,4 C1,1 15,1 15,4 L15,5.5 L11.5,5.5 L11.5,4 L4.5,4 L4.5,5.5 L1,5.5 Z M3,7 L13,7 L14,13 L2,13 Z"/></svg>
        5550147382
      </li>
      <li>
        <svg viewBox="0 0 16 14"><circle cx="8" cy="7" r="6.3" fill="none" stroke="var(--brand-red)" stroke-width="1.4"/><ellipse cx="8" cy="7" rx="2.6" ry="6.3" fill="none" stroke="var(--brand-red)" stroke-width="1.2"/><path d="M1.7,7 H14.3" stroke="var(--brand-red)" stroke-width="1.2"/></svg>
        yourname@yourwebsite.com
      </li>
      <li>
        <svg viewBox="0 0 16 14"><path d="M1,2 H15 V12 H1 Z"/><path d="M1.5,2.5 L8,8 L14.5,2.5" fill="none" stroke="var(--paper)" stroke-width="1.3"/></svg>
        www.yourwebsite.com
      </li>
    </ul>

    <p class="address">Your Long<br>Commercial or<br>business address in 2 line</p>
  </section>

</main>
</body>
</html>
```